Brimsett Gardening Fresh New Website

We are looking to create a simple fresh website for our landscaping business. The website should appeal to a 'high end' audience. We deal with a lot of Embassies and affluent clients who have extremely large gardens that are meticulously maintained. The site is about communicating our excellent landscaping and customer service skills and encouraging new clients to reach out and engage us to take care of their gardens.

The website is basically going to be our business card, it will have almost no functionality other than two 'contact us' forms, one for smaller clients and one for more detailed projects.

The website will not have a lot of written content and will have to show photos of beautifully landscaped gardens.

The main logo in black will influence the site, however, we are open to all suggestions.

We are expecting to have the following pages:
Home Page
Services
About Us
Contact Us
Showcase (photo gallery of our work)

We need someone who can code it to wordpress and be available for minor changes over a number of days. They will be simple tweaks.

```html
<!DOCTYPE html>
<html lang="en">
<head>
<meta charset="utf-8">
<title>Brimsett Gardening</title>
<link href="https://fonts.googleapis.com/css2?family=Poppins:wght@400;500;600;700&display=swap" rel="stylesheet">
<style>
:root{
  --gold:#a8781f;
  --gold-line:#c9a042;
  --yellow:#f8d44c;
  --ink:#1b1b1b;
  --text:#555;
  --white:#fff;
  --footer:#1f1f1f;
  --star:#f2c316;
}
*{box-sizing:border-box;margin:0;padding:0}
html,body{width:1200px;height:3389px;overflow:hidden}
body{position:relative;font-family:'Poppins',sans-serif;color:var(--ink);background:var(--white)}
.abs{position:absolute}

/* hero */
.hero{left:0;top:0;width:1200px;height:680px;background:linear-gradient(100deg,#24331c 0%,#3d5a2a 35%,#5a7f37 60%,#2f4a20 100%)}
.hero-glow{left:0;top:0;width:1200px;height:680px;background:radial-gradient(ellipse at 75% 30%,rgba(190,140,190,.35),transparent 45%),radial-gradient(ellipse at 45% 60%,rgba(120,170,60,.45),transparent 55%)}
.nav-line{left:0;width:1200px;height:2px;background:var(--gold-line)}
.logo-ring{left:142px;top:14px;width:122px;height:122px;border-radius:50%;border:2px solid var(--gold-line);background:#1a1f14;display:flex;align-items:center;justify-content:center;text-align:center}
.logo-name{font-weight:500;color:var(--gold-line);font-size:11px;letter-spacing:3px;line-height:1.5}
.nav{top:64px;left:588px;display:flex;gap:28px;font-size:14px;font-weight:500;color:var(--white)}
.nav-cta{left:947px;top:55px;width:111px;height:40px;background:var(--yellow);color:var(--gold);font-size:12px;font-weight:600;border-radius:3px;display:flex;align-items:center;justify-content:center}
.hero-title{left:141px;top:250px;color:var(--white);font-weight:700;font-size:46px;line-height:64px}
.hero-title em{font-style:normal;color:var(--yellow)}
.hero-title .sub{font-weight:600}
.hero-text{left:141px;top:397px;width:560px;color:var(--white);font-size:13px;line-height:21px;font-weight:500}
.btn-white{left:141px;top:486px;width:112px;height:38px;background:var(--white);border-radius:4px;font-size:12px;font-weight:500;display:flex;align-items:center;justify-content:center}
.scroll-icon{left:568px;top:600px;width:64px;height:64px;border-radius:50%;background:var(--white);box-shadow:0 4px 12px rgba(0,0,0,.15);display:flex;align-items:center;justify-content:center}

/* shared */
.section-title{width:1200px;left:0;text-align:center;font-weight:700;font-size:32px}
.rule{height:2px;width:50px;background:var(--gold)}
.btn-gold{background:var(--gold);color:var(--white);font-size:12px;font-weight:500;display:flex;align-items:center;justify-content:center;border-radius:2px}

/* about */
.about-photo{left:118px;top:717px;width:481px;height:448px;background:radial-gradient(ellipse at 50% 45%,#c9ccd0 0%,#e3e6e8 35%,#f4f5f4 60%,#fff 80%)}
.about-kicker{left:611px;top:808px;font-size:33px;font-weight:700;color:var(--gold);line-height:40px}
.about-title{left:611px;top:848px;font-size:33px;font-weight:700;line-height:40px}
.about-text{left:611px;width:450px;font-size:13px;line-height:22px;color:var(--text)}

/* services */
.services-bg{left:0;top:1380px;width:1200px;height:679px;background:linear-gradient(180deg,#fff 0%,#eef0ea 25%,#c9d2b6 60%,#8d9b62 100%)}
.tab{height:36px;top:1264px;width:158px;font-size:12px;display:flex;align-items:center;justify-content:center;border-radius:2px}
.tab-active{left:434px;background:var(--yellow);color:var(--ink)}
.tab-idle{left:607px;background:var(--gold);color:var(--white)}
.svc-photo{width:300px;height:242px}
.svc-label{height:53px;background:var(--white);display:flex;align-items:center;justify-content:center;gap:8px;font-size:15px;font-weight:500;box-shadow:0 2px 8px rgba(0,0,0,.06)}
.svc-label.featured{background:var(--yellow);height:80px;flex-direction:column;gap:4px}
.svc-label .row{display:flex;align-items:center;gap:8px}
.quote-link{font-size:12px;text-decoration:underline;margin-left:46px}

/* testimonials */
.review{width:300px;background:var(--white);border:1px solid #eee;padding:22px 20px 20px}
.review.featured{padding-top:16px;border-bottom:6px solid var(--gold);box-shadow:0 4px 14px rgba(0,0,0,.08)}
.reviewer{display:flex;align-items:center;gap:10px;margin-bottom:20px}
.review.featured .reviewer{margin-bottom:18px}
.avatar{width:58px;height:58px;border-radius:50%;background:#8a8f96;flex:none}
.reviewer-name{font-size:16px;font-weight:500}
.stars{color:var(--star);font-size:13px;letter-spacing:2px}
.review p{font-size:12.5px;line-height:21.5px;color:var(--text)}
.arrow-btn{width:42px;height:42px;border-radius:50%;background:var(--white);box-shadow:0 2px 8px rgba(0,0,0,.15);display:flex;align-items:center;justify-content:center}

/* gallery */
.gallery-item{top:2659px;width:234px;height:246px}

/* footer */
.footer{left:0;top:3050px;width:1200px;height:339px;background:var(--footer);color:var(--white)}
.foot-logo{left:100px;top:3188px;width:240px;text-align:center;color:var(--gold-line);font-weight:500;font-size:20px;letter-spacing:6px;line-height:30px}
.social{top:3279px;width:28px;height:28px;border:1.5px solid var(--white);border-radius:50%}
.foot-heading{font-size:15px;font-weight:600}
.foot-rule{height:2px;width:32px;background:var(--gold)}
.foot-link{left:512px;font-size:13px}
.contact-label{font-size:13px;font-weight:600}
.contact-text{font-size:13px;line-height:19px}
.foot-divider{left:141px;top:3351px;width:918px;height:1px;background:#444}
.copyright{left:0;width:1200px;top:3362px;text-align:center;font-size:12px}
</style>
</head>
<body>

<!-- hero -->
<div class="abs hero" role="img" aria-label="Lush manicured lawn with rounded hedges and flowering shrubs"></div>
<div class="abs hero-glow"></div>
<div class="abs nav-line" style="top:44px"></div>
<div class="abs nav-line" style="top:105px"></div>
<div class="abs logo-ring"><div class="logo-name">BRIMSETT<br>GARDENING</div></div>
<nav class="abs nav"><span>Home</span><span>About Us</span><span>Services</span><span>Our Gallery</span></nav>
<div class="abs nav-cta">CONTACT US</div>
<h1 class="abs hero-title">BRIMSETT <em>LANDSCAPING</em><br><span class="sub">Gardening</span></h1>
<p class="abs hero-text">Lorem ipsum dolor sit amet, consectetur adipiscing elit, sed do eiusmod tempor incid-idunt ut labore et dolore magna aliqua. Quis ipsum suspendisse ultrices gravida. Risus commodo viverra maecenas accumsan lacus vel facilisis.</p>
<div class="abs btn-white">READ MORE</div>
<svg class="abs" style="left:0;top:600px" width="1200" height="82" viewBox="0 0 1200 82"><path d="M0 71 Q600 -10 1200 71 L1200 82 L0 82 Z" fill="#fff"/></svg>
<div class="abs scroll-icon"><svg width="22" height="36" viewBox="0 0 22 36"><rect x="2" y="2" width="18" height="32" rx="9" fill="none" stroke="#1b1b1b" stroke-width="2.5"/><line x1="11" y1="9" x2="11" y2="16" stroke="#1b1b1b" stroke-width="2.5" stroke-linecap="round"/></svg></div>

<!-- about -->
<div class="abs about-photo" role="img" aria-label="White colonial-style house with porch and front garden"></div>
<h2 class="abs about-kicker">ABOUT</h2>
<h2 class="abs about-title">BRIMSETT GARDENING</h2>
<div class="abs rule" style="left:611px;top:901px"></div>
<p class="abs about-text" style="top:919px">Duis aute irure dolor in reprehenderit in voluptate velit esse cillum dolore eu fugiat nulla pariatur.</p>
<p class="abs about-text" style="top:969px">Lorem ipsum dolor sit amet, consectetur adipiscing elit, sed do amit eiusmod tempor incididunt ut labore et dolore magna aliqua. Ut enim ad minim veniam, quis nostrud exercitation ullamco laboris nisi ut aliquip ex ea commodo consequat.</p>
<div class="abs btn-gold" style="left:611px;top:1079px;width:153px;height:34px">READ MORE</div>

<!-- services -->
<div class="abs services-bg" role="img" aria-label="Faded garden scene with trees and a stone bench"></div>
<h2 class="abs section-title" style="top:1187px">OUR SERVICES</h2>
<div class="abs rule" style="left:575px;top:1240px"></div>
<div class="abs tab tab-active">LANDSCAPE SERVICE</div>
<div class="abs tab tab-idle">LAWN SERVICE</div>

<div class="abs svc-photo" style="left:141px;top:1330px;background:linear-gradient(180deg,#6f9fd4 0%,#a9c8e4 30%,#3e6a2c 55%,#7fa33a 100%)" role="img" aria-label="Estate house behind trees and lawn"></div>
<div class="abs svc-photo" style="left:450px;top:1330px;background:linear-gradient(180deg,#7f9e5a 0%,#4f6e36 50%,#8a8a7f 100%)" role="img" aria-label="Garden with stone planter and bench"></div>
<div class="abs svc-photo" style="left:759px;top:1330px;background:linear-gradient(160deg,#6b4a34 0%,#4a3325 60%,#5a4130 100%)" role="img" aria-label="Bare soil with pots and a trowel"></div>
<div class="abs svc-label" style="left:155px;top:1542px;width:271px"><svg width="40" height="38" viewBox="0 0 40 38"><rect x="2" y="2" width="36" height="34" fill="none" stroke="#1b1b1b" stroke-width="2"/><rect x="2" y="2" width="14" height="16" fill="#f8d44c" stroke="#1b1b1b" stroke-width="2"/><line x1="16" y1="18" x2="38" y2="18" stroke="#1b1b1b" stroke-width="2"/></svg>Design Service</div>
<div class="abs svc-label featured" style="left:463px;top:1542px;width:272px"><div class="row"><svg width="60" height="36" viewBox="0 0 60 36"><path d="M4 6 L14 6 L24 26 L50 20 L44 8 L18 10" fill="none" stroke="#1b1b1b" stroke-width="2"/><circle cx="48" cy="28" r="6" fill="none" stroke="#1b1b1b" stroke-width="2"/></svg>Mulch or Rock Install</div><span class="quote-link">Request A Quote →</span></div>
<div class="abs svc-label" style="left:773px;top:1542px;width:271px"><svg width="38" height="36" viewBox="0 0 38 36"><path d="M2 34 L20 20 L28 28 Z" fill="#f8d44c" stroke="#1b1b1b" stroke-width="2"/><line x1="24" y1="24" x2="34" y2="4" stroke="#1b1b1b" stroke-width="2"/></svg>Grading Rough</div>

<div class="abs svc-photo" style="left:141px;top:1646px;background:linear-gradient(180deg,#35552a 0%,#5a7f3a 45%,#7ea23f 100%)" role="img" aria-label="Large white mansion with open lawn"></div>
<div class="abs svc-photo" style="left:450px;top:1646px;background:linear-gradient(180deg,#3e5a26 0%,#7b6a3c 55%,#5d8a2e 100%)" role="img" aria-label="Workers rolling out fresh sod"></div>
<div class="abs svc-photo" style="left:759px;top:1646px;background:linear-gradient(180deg,#9aa090 0%,#466b30 50%,#8e8e88 100%)" role="img" aria-label="Stone retaining wall with iron railing and hedges"></div>
<div class="abs svc-label" style="left:155px;top:1858px;width:271px"><svg width="28" height="38" viewBox="0 0 28 38"><rect x="2" y="4" width="24" height="32" fill="none" stroke="#1b1b1b" stroke-width="2"/><line x1="7" y1="13" x2="21" y2="13" stroke="#1b1b1b" stroke-width="2"/><line x1="7" y1="20" x2="21" y2="20" stroke="#1b1b1b" stroke-width="2"/><line x1="7" y1="27" x2="21" y2="27" stroke="#1b1b1b" stroke-width="2"/></svg>Grading Final</div>
<div class="abs svc-label" style="left:463px;top:1858px;width:272px"><svg width="42" height="38" viewBox="0 0 42 38"><rect x="2" y="2" width="22" height="34" fill="none" stroke="#1b1b1b" stroke-width="2"/><rect x="14" y="16" width="26" height="20" fill="#f8d44c" stroke="#1b1b1b" stroke-width="2"/></svg>Sod Installation</div>
<div class="abs svc-label" style="left:773px;top:1858px;width:271px"><svg width="52" height="38" viewBox="0 0 52 38"><rect x="2" y="2" width="48" height="34" fill="#f8d44c" stroke="#1b1b1b" stroke-width="2"/><path d="M2 13 H50 M2 24 H50 M18 2 V13 M34 2 V13 M10 13 V24 M26 13 V24 M42 13 V24 M18 24 V36 M34 24 V36" stroke="#1b1b1b" stroke-width="2"/></svg>Retaining Walls</div>
<div class="abs btn-gold" style="left:524px;top:1937px;width:152px;height:33px">REQUEST A QUOTE</div>

<!-- testimonials -->
<h2 class="abs section-title" style="top:2134px">WHAT OUR CLIENTS SAY</h2>
<div class="abs rule" style="left:575px;top:2187px"></div>
<div class="abs arrow-btn" style="left:75px;top:2371px"><svg width="12" height="16" viewBox="0 0 12 16"><path d="M9 2 L3 8 L9 14" fill="none" stroke="#1b1b1b" stroke-width="2.5"/></svg></div>
<div class="abs arrow-btn" style="left:1083px;top:2371px"><svg width="12" height="16" viewBox="0 0 12 16"><path d="M3 2 L9 8 L3 14" fill="none" stroke="#1b1b1b" stroke-width="2.5"/></svg></div>

<div class="abs review" style="left:141px;top:2240px;min-height:267px">
  <div class="reviewer"><div class="avatar" role="img" aria-label="Client portrait" style="background:#5aa7d6"></div><div><div class="reviewer-name">Owen Carrow</div><div class="stars">★★★★★</div></div></div>
  <p>Lorem ipsum dolor sit amet, consectetur adipiscing elit, sed do eiusmod tempor incididunt ut labore et dolore magna aliqua. Ut enim ad minim veniam ut aut reiciendis voluptatibus maiores alias ut aut reiciendis voluptatibus.</p>
</div>
<div class="abs review featured" style="left:450px;top:2212px;min-height:272px">
  <div class="reviewer"><div class="avatar" role="img" aria-label="Client portrait" style="background:#7a6f66"></div><div><div class="reviewer-name">Nadia Pell</div><div class="stars">★★★★★</div></div></div>
  <p>Sed ut perspiciatis unde omnis iste natus error sit voluptatem accusantium doloremque laudantium, totam rem aperiam, eaque ipsa quae ab illo AMIT inventore veritatis et quasi architecto beatae vitae dicta sunt explicabo. Nemo enim ipsam voluptatem.</p>
</div>
<div class="abs review" style="left:759px;top:2240px;min-height:267px">
  <div class="reviewer"><div class="avatar" role="img" aria-label="Client portrait" style="background:#2e3a36"></div><div><div class="reviewer-name">Theo R</div><div class="stars">★★★★★</div></div></div>
  <p>Lorem ipsum dolor sit amet, consectetur adipiscing elit, sed do eiusmod tempor incididunt ut labore et dolore magna aliqua. Ut enim ad minim veniam ut aut reiciendis voluptatibus maiores alias ut aut reiciendis voluptatibus.</p>
</div>

<!-- gallery -->
<h2 class="abs section-title" style="top:2583px">WORK GALLERY</h2>
<div class="abs rule" style="left:575px;top:2635px"></div>
<div class="abs gallery-item" style="left:0;background:linear-gradient(180deg,#c9d9e6 0%,#b59a6a 40%,#6f9a2e 70%,#8db83a 100%)" role="img" aria-label="Villas above a sloping lawn"></div>
<div class="abs gallery-item" style="left:241px;background:linear-gradient(180deg,#8a5a3a 0%,#9a8466 40%,#6e6252 75%,#4e7a2a 100%)" role="img" aria-label="Curved stone wall with flower beds"></div>
<div class="abs gallery-item" style="left:483px;background:linear-gradient(180deg,#9fb5cc 0%,#c9b08a 40%,#6f7a8c 75%,#4e6e34 100%)" role="img" aria-label="Cottage front with allium flowers"></div>
<div class="abs gallery-item" style="left:724px;background:linear-gradient(180deg,#3f6a2a 0%,#a05454 35%,#9a8a80 70%,#6e5a52 100%)" role="img" aria-label="Stone steps through flowering garden"></div>
<div class="abs gallery-item" style="left:966px;background:linear-gradient(180deg,#b8c6cf 0%,#3d6a2a 40%,#8a8070 75%,#5d8a2e 100%)" role="img" aria-label="Paved path leading to a house"></div>
<div class="abs btn-gold" style="left:522px;top:2930px;width:153px;height:35px">VIEW ALL</div>

<!-- footer -->
<footer class="abs footer"></footer>
<div class="abs foot-logo">BRIMSETT<br>GARDENING</div>
<div class="abs social" style="left:156px" aria-label="Social link"></div>
<div class="abs social" style="left:190px" aria-label="Social link"></div>
<div class="abs social" style="left:224px" aria-label="Social link"></div>
<div class="abs social" style="left:258px" aria-label="Social link"></div>

<div class="abs foot-heading" style="left:512px;top:3101px;color:#fff">QUICK LINKS</div>
<div class="abs foot-rule" style="left:512px;top:3128px"></div>
<div class="abs foot-link" style="top:3150px;color:#fff">Home</div>
<div class="abs foot-link" style="top:3186px;color:#fff">Services</div>
<div class="abs foot-link" style="top:3222px;color:#fff">Gallery</div>
<div class="abs foot-link" style="top:3257px;color:#fff">About Us</div>
<div class="abs foot-link" style="top:3293px;color:#fff">Contact Us</div>

<div class="abs foot-heading" style="left:849px;top:3101px;color:#fff">CONTACT DETAILS</div>
<div class="abs foot-rule" style="left:849px;top:3128px"></div>
<svg class="abs" style="left:850px;top:3149px" width="28" height="28" viewBox="0 0 28 28"><circle cx="14" cy="14" r="11" fill="none" stroke="#fff" stroke-width="1.6"/><path d="M3 14 H25 M14 3 C8 9 8 19 14 25 M14 3 C20 9 20 19 14 25" fill="none" stroke="#fff" stroke-width="1.4"/></svg>
<div class="abs contact-text" style="left:886px;top:3145px;color:#fff">123, Building Name, Street<br>City, State XY 123456</div>
<svg class="abs" style="left:850px;top:3212px" width="28" height="28" viewBox="0 0 28 28"><path d="M6 3 L11 3 L13 9 L10 11 C11 15 13 17 17 18 L19 15 L25 17 L25 22 C25 24 23 25 21 25 C11 24 4 17 3 7 C3 5 4 3 6 3 Z" fill="none" stroke="#fff" stroke-width="1.6"/></svg>
<div class="abs contact-label" style="left:890px;top:3208px;color:#fff">Phone</div>
<div class="abs contact-text" style="left:890px;top:3226px;color:#fff">(123) 456-7890</div>
<svg class="abs" style="left:850px;top:3274px" width="28" height="28" viewBox="0 0 28 28"><rect x="3" y="7" width="22" height="17" fill="none" stroke="#fff" stroke-width="1.6"/><path d="M3 7 L14 16 L25 7" fill="none" stroke="#fff" stroke-width="1.6"/></svg>
<div class="abs contact-label" style="left:890px;top:3270px;color:#fff">Email</div>
<div class="abs contact-text" style="left:890px;top:3288px;color:#fff">info@brimsettgardening.com</div>

<div class="abs foot-divider"></div>
<div class="abs copyright" style="color:#fff">© 2024 Brimsett Gardening. All Rights Reserved</div>

</body>
</html>
```